Tide & Thistle Website Creation For Online Spirits Sales via MerrowVats.com

Want a Website developed that I will use to partner with Merrow Vats to sell my signature rum online. Merrow Vats will add the final code to make the website an e-commerce site. Website should have links to Social media pages, recipies, About, news and events, products. I have he domain name already just need a designer to make the website look professional. Need website capable of being viewed on iPhone and Android devices. Please use the color scheme that is on the label. The brand motto is: Celebrate Life With Family old and new friends. The bottle sent in the images will be replaced with and actual high resolution image of the bottle when it is produce on 27 DEC 21. Can give the selected designer access to develop the website. I have the hostbramble.com domain name. Final code will be added by a designer from MerrowVats.com to make it a e-commerce store.
Updates

I added more information to refine the design I wanted. I should have had this information available to the designers when I started the project.

Target Market(s)

Target Market is 25-50 year old who drink rum

Industry/Entity Type

Spirits. Using Website to sell Rum online

Number of Pages Required

1 page

Font styles to use
Sans Serif

Colors
00AB8E
00BBA5
67D7C9
C6EFE9
E9F9F6

Requirements
Must have
• Must look elegant and of high class. Rum is being market as a premium unnamed rum.
Nice to have
• Video of people drinking, smiling and celebrating

```html
<!DOCTYPE html>
<html lang="en">
<head>
<meta charset="utf-8">
<title>Tide &amp; Thistle — Premium Rum</title>
<link href="https://fonts.googleapis.com/css2?family=Roboto+Slab:wght@700;800&family=Work+Sans:wght@400;500;600;700&display=swap" rel="stylesheet">
<style>
:root{
  --green:#00a888;
  --green-dark:#1a9a7e;
  --teal:#00bba5;
  --mint:#67d7c9;
  --mint-pale:#c6efe9;
  --mint-faint:#e9f9f6;
  --ink:#151515;
  --dark:#141414;
  --text:#2b2b2b;
  --muted:#555;
  --star:#f5a623;
  --white:#fff;
}
*{margin:0;padding:0;box-sizing:border-box}
html,body{width:1200px;height:4258px;overflow:hidden;background:var(--white)}
body{font-family:"Work Sans",Arial,sans-serif;color:var(--text)}
.page{position:relative;width:1200px;height:4258px;overflow:hidden}
.abs{position:absolute}
.slab{font-family:"Roboto Slab",Georgia,serif;font-weight:800}

/* header */
.top-line{left:0;top:0;width:1200px;height:4px;background:var(--green)}
.util-bar{left:826px;top:0;width:374px;height:38px;background:var(--green);border-bottom-left-radius:34px;display:flex;align-items:center;justify-content:center;gap:12px;color:#fff;font-size:14px;font-weight:600}
.util-dot{width:11px;height:11px;border-radius:50%;background:#fff}
.util-sep{width:1px;height:14px;background:#fff;margin:0 4px}
.brand{left:110px;top:18px;width:170px;display:flex;flex-direction:column;align-items:center;gap:6px}
.brand-mark{width:48px;height:48px;border-radius:50%;background:var(--ink)}
.brand-name{font-family:"Work Sans",sans-serif;font-weight:600;font-size:22px;color:var(--ink);letter-spacing:.5px;white-space:nowrap}
.nav{top:66px;left:0;width:1200px;font-size:14px;font-weight:700;color:var(--ink);letter-spacing:.3px}
.nav a{position:absolute;color:inherit;text-decoration:none;white-space:nowrap}
.nav a.active{color:var(--green)}

/* hero */
.hero-photo{left:0;top:104px;width:1200px;height:700px;background:linear-gradient(180deg,#2a3a44 0%,#4b5a5e 25%,#c98a3c 48%,#f0a43a 55%,#7a4a24 66%,#3a2c24 80%,#2a241f 100%)}
.hero-curve{left:0;top:640px}
.hero-title{left:112px;top:310px;font-size:44px;color:#fff;letter-spacing:.5px}
.hero-copy{left:112px;top:374px;width:600px;font-size:17px;line-height:28px;font-weight:700;color:#fff}
.btn-solid{display:flex;align-items:center;justify-content:center;background:var(--green);color:#fff;font-weight:700;font-size:16px;border-radius:26px;letter-spacing:.3px}
.hero-btn{left:112px;top:481px;width:146px;height:46px}
.arrow{width:34px;height:34px;border-radius:50%;background:#fff;display:flex;align-items:center;justify-content:center;box-shadow:0 2px 6px rgba(0,0,0,.2)}
.arrow-outline{border:2px solid var(--green)}
.arrow-green{background:var(--green)}
.hero-bottle{left:817px;top:278px;width:172px;height:510px}

/* about */
.about-bg{left:0;top:793px;width:1200px;height:650px;background:linear-gradient(180deg,#fff 0%,#f1f2f2 30%,#e7e8e6 100%)}
.about-circle{left:112px;top:902px;width:404px;height:404px;border-radius:50%;border:6px solid #fff;background:radial-gradient(circle at 45% 40%,#c58a5a,#6b3a2a 60%,#2c1a16);box-shadow:0 4px 14px rgba(0,0,0,.2)}
.play{left:280px;top:1070px;width:68px;height:68px;border-radius:50%;border:3px solid #fff;background:rgba(255,255,255,.25);display:flex;align-items:center;justify-content:center}
.play span{width:44px;height:44px;border-radius:50%;background:#fff;display:flex;align-items:center;justify-content:center}
.about-bottle{left:410px;top:896px;width:142px;height:413px}
.about-title{left:598px;top:912px;font-size:34px;color:var(--ink)}
.accent{color:var(--green)}
.about-copy{left:598px;top:985px;width:490px;font-size:13.5px;line-height:25px;color:#444;text-align:justify}
.about-copy p+p{margin-top:18px}
.btn-outline{display:flex;align-items:center;justify-content:center;border:3px solid var(--green);color:var(--ink);font-weight:700;font-size:16px;border-radius:26px;background:#fff}
.about-btn{left:598px;top:1240px;width:146px;height:48px}

/* featured */
.featured{left:0;top:1435px;width:1200px;height:620px;background:var(--dark)}
.section-title{left:0;width:1200px;text-align:center;font-size:36px;letter-spacing:.3px}
.feat-title{top:1500px;color:#fff}
.card{top:1598px;width:232px;height:300px;background:#fff}
.card-bottle{position:absolute;left:78px;top:38px;width:76px;height:230px;border-radius:24px 24px 14px 14px}
.rum-gold{background:linear-gradient(180deg,#d7c7a0 0%,#d7c7a0 20%,#c98a35 32%,#b87028 60%,#a6c9bd 62%,#eaf2ef 80%,#c68537 100%)}
.rum-red{background:linear-gradient(180deg,#222 0%,#222 20%,#c9571f 32%,#9a3214 60%,#eaf2ef 62%,#f4f4f0 80%,#b44a1d 100%)}
.card-meta{width:232px;text-align:center;color:#fff}
.stars{color:var(--star);font-size:13px;letter-spacing:1px}
.card-name{font-weight:700;font-size:16px;margin-top:5px;letter-spacing:.3px}
.card-price{font-weight:700;font-size:14px;margin-top:6px}
.quick{position:absolute;top:156px;width:34px;height:34px;border-radius:50%;display:flex;align-items:center;justify-content:center}

/* recipes */
.rec-title{top:2180px;color:var(--ink)}
.rec-side{top:2339px;width:187px;height:223px;border:4px solid #fff;box-shadow:0 2px 10px rgba(0,0,0,.25)}
.rec-main{left:299px;top:2271px;width:601px;height:359px;border:6px solid var(--green);background:linear-gradient(135deg,#3a2e1e,#15110c 55%,#2b1a0e)}
.rec-caption{left:333px;top:2515px;color:#fff}
.rec-caption h3{font-size:19px;font-weight:700;letter-spacing:.5px}
.rec-caption p{font-size:13.5px;line-height:23px;margin-top:12px;width:560px}

/* testimonials */
.testi-band{left:0;top:2740px;width:1200px;height:520px;background:var(--green-dark)}
.testi-title{top:2832px;color:#fff}
.testi-card{top:2919px;width:480px;height:238px;background:#fff;border-radius:4px;padding:20px 22px}
.quote{font-family:"Roboto Slab",serif;font-size:62px;line-height:50px;color:var(--green);font-weight:800}
.testi-text{font-size:13.5px;line-height:25px;color:#555;margin-top:8px}
.testi-text b{color:var(--ink)}
.person{display:flex;align-items:center;gap:20px;margin-top:14px}
.avatar{width:58px;height:58px;border-radius:50%;background:linear-gradient(135deg,#d8c6b8,#6e5a4f)}
.person-name{font-weight:700;font-size:18px;color:var(--ink)}

/* events */
.ev-title{top:3350px;color:var(--ink)}
.ev{top:3432px;width:302px;text-align:center}
.ev-photo{width:302px;height:205px}
.ev-date{color:var(--green);font-size:14px;font-weight:500;margin-top:22px}
.ev-name{font-weight:700;font-size:19px;line-height:26px;color:var(--ink);margin-top:8px}
.ev-rule{top:3432px;width:1px;height:298px;background:#ccc}

/* footer */
.footer{left:0;top:3810px}
.f-brand{left:500px;top:3868px;width:200px;display:flex;flex-direction:column;align-items:center;gap:10px}
.f-brand .brand-mark{background:#fff;width:52px;height:52px}
.f-brand .brand-name{color:#fff;font-size:24px}
.f-head{top:3995px;color:#fff;font-weight:700;font-size:17px}
.f-links{top:4045px;list-style:none;color:#fff;font-size:14px;line-height:29.3px}
.f-input{left:616px;top:4052px;width:326px;height:50px;border:2px solid #fff;border-radius:26px;color:#fff;font-size:13px;display:flex;align-items:center;padding-left:22px}
.f-btn{left:954px;top:4052px;width:134px;height:50px}
.f-contact{left:616px;top:4131px;color:#fff;font-size:14px;font-weight:500;display:flex;align-items:center;gap:14px}
.f-contact .sep{width:1px;height:14px;background:#fff}
.f-rule{left:111px;top:4198px;width:977px;height:1px;background:#444}
.copy{left:0;top:4219px;width:1200px;text-align:center;color:#fff;font-size:13px}
</style>
</head>
<body>
<div class="page">

  <!-- header -->
  <div class="abs top-line"></div>
  <div class="abs util-bar">
    <span class="util-dot"></span><span class="util-dot"></span><span class="util-dot"></span>
    <span class="util-sep"></span>
    <svg width="16" height="16" viewBox="0 0 16 16"><circle cx="8" cy="8" r="7" fill="none" stroke="#fff" stroke-width="1.6"/><circle cx="8" cy="6.5" r="2.4" fill="#fff"/><path d="M3.6 12.8c1-2 2.6-3 4.4-3s3.4 1 4.4 3" fill="#fff"/></svg>
    <svg width="16" height="15" viewBox="0 0 16 15"><path d="M8 14L1.6 7.6A3.8 3.8 0 0 1 8 2.6a3.8 3.8 0 0 1 6.4 5z" fill="#fff"/></svg>
    <span style="display:flex;align-items:center;gap:2px"><svg width="18" height="15" viewBox="0 0 18 15"><path d="M1 1h3l2 9h9l2-7H5" fill="none" stroke="#fff" stroke-width="1.8"/><circle cx="7" cy="13" r="1.5" fill="#fff"/><circle cx="14" cy="13" r="1.5" fill="#fff"/></svg>(0)</span>
  </div>
  <div class="abs brand"><span class="brand-mark"></span><span class="brand-name">TIDE &amp; THISTLE</span></div>
  <nav class="abs nav">
    <a class="active" style="left:428px">HOME</a>
    <a style="left:502px">ABOUT US</a>
    <a style="left:608px">OUR PRODUCTS</a>
    <a style="left:757px">OUR RECIPES</a>
    <a style="left:888px">LATEST BLOG</a>
    <a style="left:1018px">CONTACT</a>
  </nav>

  <!-- hero -->
  <div class="abs hero-photo" role="img" aria-label="Tropical beach at sunset with palm trees and calm water"></div>
  <svg class="abs hero-curve" width="1200" height="170" viewBox="0 0 1200 170">
    <path d="M0 30 Q600 220 1200 40 L1200 170 L0 170Z" fill="#fff"/>
    <path d="M0 30 Q600 220 1200 40 L1200 50 Q600 200 0 40Z" fill="var(--green)"/>
  </svg>
  <h1 class="abs slab hero-title">WELCOME TO TIDE &amp; THISTLE</h1>
  <p class="abs hero-copy">Celebrate Life With Family, old and new friends. The bottle sent in the images will be replaced with an actual high resolution image of the bottle when it is produced on 27 DEC 21.</p>
  <div class="abs btn-solid hero-btn">SHOP NOW</div>
  <div class="abs arrow" style="left:34px;top:400px"><svg width="10" height="12"><path d="M7 1L2 6l5 5" fill="none" stroke="var(--green)" stroke-width="2.4"/></svg></div>
  <div class="abs arrow" style="left:1130px;top:400px"><svg width="10" height="12"><path d="M3 1l5 5-5 5" fill="none" stroke="var(--green)" stroke-width="2.4"/></svg></div>
  <div class="abs hero-bottle rum-gold" role="img" aria-label="Tide &amp; Thistle rum bottle with amber liquid and pale green label" style="border-radius:70px 70px 30px 30px"></div>

  <!-- about -->
  <div class="abs about-bg" role="img" aria-label="Soft background of whisky glasses on a light wooden bar"></div>
  <div class="abs about-circle" role="img" aria-label="Video still of friends celebrating with drinks"></div>
  <div class="abs play"><span><svg width="14" height="16"><path d="M2 1l11 7-11 7z" fill="var(--green)"/></svg></span></div>
  <div class="abs about-bottle rum-gold" role="img" aria-label="Tide &amp; Thistle rum bottle" style="border-radius:50px 50px 20px 20px"></div>
  <h2 class="abs slab about-title"><span class="accent">ABOUT</span> TIDE &amp; THISTLE</h2>
  <div class="abs about-copy">
    <p>Es un hecho establecido hace demasiado tiempo que un lector se distraerá con el contenido del texto de un sitio mientras que mira su diseñ unto de usar Lorem Ipsumea.</p>
    <p>Hecho establecido hace demasiado tiempo que un lector se distraerá con el contenido del texto de un sitio mientras que mira su diseño. El punto de usar Lorem Ipsum es que tiene una distribución más o menos normal de las letras, al contrario de usar textos como por ejemploea.</p>
  </div>
  <div class="abs btn-outline about-btn">SHOP NOW</div>

  <!-- featured -->
  <div class="abs featured"></div>
  <svg class="abs" style="left:0;top:1400px" width="1200" height="45" viewBox="0 0 1200 45">
    <path d="M0 30 L40 22 L80 28 L120 18 L170 26 L210 15 L260 24 L300 12 L350 22 L400 14 L450 25 L500 16 L550 23 L600 10 L650 21 L700 14 L750 24 L800 12 L850 22 L900 15 L950 26 L1000 13 L1050 22 L1100 16 L1150 24 L1200 14 L1200 45 L0 45Z" fill="var(--dark)"/>
  </svg>
  <h2 class="abs slab section-title feat-title">FEATURED PRODUCTS</h2>
  <div class="abs card" style="left:111px"><div class="card-bottle rum-gold" role="img" aria-label="Rum bottle"></div></div>
  <div class="abs card" style="left:360px"><div class="card-bottle rum-red" role="img" aria-label="Dark rum bottle"></div>
    <div class="quick" style="left:74px;background:var(--ink)"><svg width="14" height="13" viewBox="0 0 16 15"><path d="M8 14L1.6 7.6A3.8 3.8 0 0 1 8 2.6a3.8 3.8 0 0 1 6.4 5z" fill="#fff"/></svg></div>
    <div class="quick" style="left:116px;background:var(--green)"><svg width="16" height="13" viewBox="0 0 18 15"><path d="M1 1h3l2 9h9l2-7H5" fill="none" stroke="#fff" stroke-width="1.8"/><circle cx="7" cy="13" r="1.5" fill="#fff"/><circle cx="14" cy="13" r="1.5" fill="#fff"/></svg></div>
  </div>
  <div class="abs card" style="left:608px"><div class="card-bottle rum-gold" role="img" aria-label="Rum bottle"></div></div>
  <div class="abs card" style="left:856px"><div class="card-bottle rum-red" role="img" aria-label="Dark rum bottle"></div></div>
  <div class="abs card-meta" style="left:111px;top:1912px"><div class="stars">★★★★★</div><div class="card-name">PRODUCT TITLE HERE</div><div class="card-price">$83.99</div></div>
  <div class="abs card-meta" style="left:360px;top:1912px"><div class="stars">★★★★★</div><div class="card-name">PRODUCT TITLE HERE</div><div class="card-price">$83.99</div></div>
  <div class="abs card-meta" style="left:608px;top:1912px"><div class="stars">★★★★★</div><div class="card-name">PRODUCT TITLE HERE</div><div class="card-price">$83.99</div></div>
  <div class="abs card-meta" style="left:856px;top:1912px"><div class="stars">★★★★★</div><div class="card-name">PRODUCT TITLE HERE</div><div class="card-price">$83.99</div></div>
  <svg class="abs" style="left:0;top:2050px" width="1200" height="40" viewBox="0 0 1200 40">
    <path d="M0 0 L1200 0 L1200 16 L1150 8 L1100 18 L1050 10 L1000 20 L950 12 L900 22 L850 14 L800 24 L750 15 L700 22 L650 12 L600 20 L550 14 L500 24 L450 15 L400 22 L350 12 L300 20 L250 14 L200 24 L150 16 L100 22 L50 12 L0 20Z" fill="var(--dark)"/>
  </svg>

  <!-- recipes -->
  <h2 class="abs slab section-title rec-title"><span class="accent">OUR</span> RECIPES</h2>
  <div class="abs rec-side" style="left:-4px;background:linear-gradient(135deg,#1a0d08,#7a2a14 50%,#1a0d08)" role="img" aria-label="Glass of dark rum beside a decanter"></div>
  <div class="abs rec-side" style="left:1013px;background:linear-gradient(135deg,#2a2520,#8a6a3a 50%,#1b1712)" role="img" aria-label="Crystal decanter and glasses with ice"></div>
  <div class="abs rec-main" role="img" aria-label="Rum being poured into snifter glasses"></div>
  <div class="abs rec-caption"><h3>LOREM IPSUM ES SIMPLEME</h3><p>Es un hecho establecido hace demasiado tiempo que un lector se dist raerá con el contenido del textoea.</p></div>
  <div class="abs arrow arrow-green" style="left:228px;top:2434px"><svg width="10" height="12"><path d="M7 1L2 6l5 5" fill="none" stroke="#fff" stroke-width="2.4"/></svg></div>
  <div class="abs arrow arrow-green" style="left:937px;top:2434px"><svg width="10" height="12"><path d="M3 1l5 5-5 5" fill="none" stroke="#fff" stroke-width="2.4"/></svg></div>

  <!-- testimonials -->
  <div class="abs testi-band"></div>
  <svg class="abs" style="left:0;top:2715px" width="1200" height="35" viewBox="0 0 1200 35">
    <path d="M0 24 L60 14 L120 22 L180 10 L240 20 L300 8 L360 18 L420 10 L480 22 L540 12 L600 20 L660 8 L720 18 L780 12 L840 22 L900 10 L960 20 L1020 12 L1080 22 L1140 8 L1200 18 L1200 35 L0 35Z" fill="var(--green-dark)"/>
  </svg>
  <svg class="abs" style="left:0;top:3255px" width="1200" height="30" viewBox="0 0 1200 30">
    <path d="M0 0 L1200 0 L1200 14 L1140 22 L1080 10 L1020 20 L960 12 L900 24 L840 12 L780 20 L720 10 L660 22 L600 12 L540 20 L480 10 L420 22 L360 12 L300 20 L240 10 L180 22 L120 12 L60 20 L0 10Z" fill="var(--green-dark)"/>
  </svg>
  <h2 class="abs slab section-title testi-title">TESTIMONIALS</h2>
  <div class="abs testi-card" style="left:111px">
    <div class="quote">“</div>
    <p class="testi-text">"Always ready to find solutions and innovative ways to promote our products, <b>Tide &amp; Thistle</b> has proven to be an invaluable partner for us".</p>
    <div class="person"><span class="avatar" role="img" aria-label="Customer portrait"></span><div><div class="person-name">Rowan Pell</div><div class="stars">★★★★★</div></div></div>
  </div>
  <div class="abs testi-card" style="left:608px">
    <div class="quote">“</div>
    <p class="testi-text">"<b>Tide &amp; Thistle</b> is the go-to for e-commerce within the wine and spirits space. My brand's success would not be where it is today without the comprehensive solution...</p>
    <div class="person"><span class="avatar" role="img" aria-label="Customer portrait"></span><div><div class="person-name">Gideon Marsh</div><div class="stars">★★★★★</div></div></div>
  </div>
  <div class="abs arrow" style="left:34px;top:3021px"><svg width="10" height="12"><path d="M7 1L2 6l5 5" fill="none" stroke="var(--green)" stroke-width="2.4"/></svg></div>
  <div class="abs arrow" style="left:1130px;top:3021px"><svg width="10" height="12"><path d="M3 1l5 5-5 5" fill="none" stroke="var(--green)" stroke-width="2.4"/></svg></div>

  <!-- events -->
  <h2 class="abs slab section-title ev-title"><span class="accent">LATEST</span> EVENTS</h2>
  <div class="abs ev" style="left:111px"><div class="ev-photo" role="img" aria-label="Friends dancing at an evening party" style="background:linear-gradient(135deg,#2a1a12,#8a4a2a 50%,#1e140e)"></div><div class="ev-date">14 DEC 2021</div><div class="ev-name">Sed ut perspiciatis undeom<br>lorum natus error</div></div>
  <div class="abs ev-rule" style="left:431px"></div>
  <div class="abs ev" style="left:450px"><div class="ev-photo" role="img" aria-label="Cocktail glass on a candlelit table" style="background:linear-gradient(135deg,#3a2a1a,#b07a3a 50%,#2a1e12)"></div><div class="ev-date">14 DEC 2021</div><div class="ev-name">Sed ut perspiciatis undeom<br>lorum natus error</div></div>
  <div class="abs ev-rule" style="left:768px"></div>
  <div class="abs ev" style="left:787px"><div class="ev-photo" role="img" aria-label="Group toasting at an outdoor dinner" style="background:linear-gradient(135deg,#1e1a18,#7a4a2a 50%,#181412)"></div><div class="ev-date">14 DEC 2021</div><div class="ev-name">Sed ut perspiciatis undeom<br>lorum natus error</div></div>

  <!-- footer -->
  <svg class="abs footer" width="1200" height="448" viewBox="0 0 1200 448">
    <path d="M0 140 Q600 -60 1200 140 L1200 448 L0 448Z" fill="var(--dark)"/>
    <path d="M0 140 Q600 -60 1200 140" fill="none" stroke="var(--green)" stroke-width="6"/>
  </svg>
  <div class="abs f-brand"><span class="brand-mark"></span><span class="brand-name">TIDE &amp; THISTLE</span></div>
  <div class="abs f-head" style="left:111px">Quick Links</div>
  <div class="abs f-head" style="left:360px">Other Links</div>
  <div class="abs f-head" style="left:616px">Join Our Newsletter</div>
  <ul class="abs f-links" style="left:111px"><li>Home</li><li>About Us</li><li>Our Products</li><li>Our Recipes</li><li>Contact Us</li></ul>
  <ul class="abs f-links" style="left:360px"><li>Latest Blog</li><li>Shipping &amp; Returns</li><li>FAQ</li><li>Contact</li></ul>
  <div class="abs f-input">Enter Your Email Here</div>
  <div class="abs btn-solid f-btn">SHOP NOW</div>
  <div class="abs f-contact">
    <svg width="14" height="14" viewBox="0 0 14 14"><path d="M3 1l2.5 3-1.5 1.5a8 8 0 0 0 4.5 4.5L10 8.5l3 2.5-1.5 2A11 11 0 0 1 1 2.5z" fill="var(--green)"/></svg>
    <span>321 - 654 - 0987</span><span class="sep"></span>
    <svg width="16" height="12" viewBox="0 0 16 12"><rect x="0" y="0" width="16" height="12" rx="1.5" fill="var(--green)"/><path d="M1 1l7 5 7-5" fill="none" stroke="var(--dark)" stroke-width="1.4"/></svg>
    <span>info@tideandthistle.com</span><span class="sep"></span>
    <span class="util-dot"></span><span class="util-dot"></span><span class="util-dot"></span>
  </div>
  <div class="abs f-rule"></div>
  <div class="abs copy">© 2021 TIDE &amp; THISTLE. All Rights Reserved</div>

</div>
</body>
</html>
```